Ridge Lass Crew (Flyer)

I want a flyer to advertise my service.
Details below, and logo's to use are attached.

A girls only after school program, 11-14yrs, as OSHC is no longer avail, dedicated to coaching & mentoring our girls into strong, independent young women.

The Brainchild of Rebecca Folwin, Ridge Lass Crew was created to address the growing demand for after school/school holiday supervision for kids moving from primary into high school, when OSHC ceases to exist.
With over 12 years experience mentoring and coaching young women in the corporate world, Bec decided to leave her role as a Director with Tarrant Trust, and follow her passion.
Bec, along with her sister Lorraine, who has over 10 years experience in local communities as a Youth Worker, and is also a qualified Enrolled Nurse, embarked on building a program designed to keep parents happy (by knowing their girls are safe) and dedicated to coaching and mentoring our girls into strong, independent young women.
Open every afternoon and during school holidays, we look to offer;
- Daily meditation
- Healthy snacks
- Dedicated homework time
- Organised group activity, led by qualified instructors (yoga, fitness class, soccer etc)
- Regular guests speakers, addressing issues/concerns for young people today
- SOCIAL MEDIA FREE ZONE

Located 87 Pelham Pde, Castlemere Vale (across from Crestmoor Day Clinic)
Open 3-6pm Monday to Friday

Facebook page: http://fb.example/ridgelasscrew
Email: info@ridgelasscrew.example.au
Mobile: 0455817396

Target Market(s)

Parents of teenage girls, teenage girls 11-14 years

Industry/Entity Type

School

Font styles to use
Sans Serif

Colors
b768aa
e667a6

Requirements
Must have
• What progam is - see brief
• Who runs it
Should not have
• Not be too busy, not overly mature images

```html
<!DOCTYPE html>
<html lang="en">
<head>
<meta charset="utf-8">
<title>Ridge Lass Crew – After School Program Flyer</title>
<link rel="stylesheet" href="https://fonts.googleapis.com/css2?family=Andada+Pro:wght@700&family=Open+Sans:wght@700;800&family=Marcellus&family=Bitter:wght@800&family=Cinzel:wght@700&family=Crimson+Text:ital@1&family=Alegreya+Sans:wght@500&family=Roboto+Condensed:wght@400&display=swap">
<style>
  :root {
    --orchid: #b768aa;
    --orchid-box: #b46aa6;
    --pink: #e667a6;
    --pink-band: #e066a2;
    --violet-deep: #8e1fc4;
    --violet-light: #c24fe0;
    --ink: #1c1418;
    --white: #ffffff;
    --social-square: #3b5a9a;
  }
  * { margin: 0; padding: 0; box-sizing: border-box; }
  html, body { width: 848px; height: 1200px; overflow: hidden; background: #fff; }
  .flyer { position: relative; width: 848px; height: 1200px; overflow: hidden; background: var(--orchid); }

  .hero-photo {
    position: absolute; left: 0; top: 0; width: 848px; height: 488px;
    background: radial-gradient(ellipse at 55% 45%, var(--violet-light), var(--violet-deep) 75%);
  }
  .brand-card {
    position: absolute; left: 32px; top: 36px; width: 260px; height: 360px;
    background: var(--white); display: flex; align-items: center; justify-content: center;
  }
  .brand-name {
    font-family: "Bitter", serif; font-weight: 800; font-size: 40px; line-height: 1.1;
    color: var(--pink); text-align: center;
  }
  .headline-box {
    position: absolute; left: 412px; top: 62px; width: 388px; height: 330px;
    background: var(--orchid-box); border-radius: 14px; text-align: center; color: var(--white);
  }
  .headline {
    font-family: "Andada Pro", serif; font-weight: 700; font-size: 45px; line-height: 64px;
    margin-top: 38px; white-space: nowrap;
  }
  .age-range { font-family: "Open Sans", sans-serif; font-weight: 800; font-size: 68px; line-height: 76px; margin-top: 6px; }
  .age-note { font-family: "Open Sans", sans-serif; font-weight: 700; font-size: 21px; color: var(--ink); margin-top: 4px; }

  .founder-band {
    position: absolute; left: 0; top: 488px; width: 848px; height: 162px;
    background: var(--pink-band); text-align: center; padding-left: 36px;
  }
  .founder-line { font-family: "Marcellus", serif; font-size: 39px; line-height: 41px; color: var(--ink); margin-top: 8px; }
  .mission { font-family: "Bitter", serif; font-weight: 800; font-size: 27px; line-height: 34px; color: var(--white); margin-top: 2px; }

  .offer-heading {
    position: absolute; left: 0; width: 818px; top: 650px; text-align: center;
    font-family: "Cinzel", serif; font-weight: 700; font-size: 44px; line-height: 56px;
    color: var(--ink); font-variant: small-caps;
  }
  .offer-list { position: absolute; left: 27px; top: 700px; list-style: none; }
  .offer-list li {
    position: relative; padding-left: 31px; font-family: "Crimson Text", serif; font-style: italic;
    font-size: 31px; line-height: 40px; color: var(--white); margin-bottom: 2px;
  }
  .offer-list li svg { position: absolute; left: 0; top: 13px; }

  .hours-days, .hours-time {
    position: absolute; left: 0; width: 848px; text-align: center;
    font-family: "Alegreya Sans", sans-serif; font-weight: 500; font-size: 38px; line-height: 44px;
  }
  .hours-days { top: 998px; padding-left: 72px; color: var(--ink); }
  .hours-time { top: 1040px; padding-left: 26px; color: var(--white); }

  .contact-bar {
    position: absolute; left: 0; top: 1086px; width: 848px; height: 114px; background: var(--pink-band);
    font-family: "Roboto Condensed", sans-serif; color: var(--white);
  }
  .contact-bar svg.icon { position: absolute; }
  .contact-text { position: absolute; font-size: 19px; line-height: 25px; white-space: nowrap; }
  .contact-note { font-size: 13px; }
</style>
</head>
<body>
<main class="flyer">
  <div class="hero-photo" role="img" aria-label="Purple background of thin web lines and motivational words with a smiling girl raising her arms"></div>

  <div class="brand-card"><p class="brand-name">Ridge<br>Lass<br>Crew</p></div>

  <section class="headline-box">
    <h1 class="headline">A Girls Only After<br>School Program</h1>
    <p class="age-range">11-14yrs</p>
    <p class="age-note">as OSHC is no longer available</p>
  </section>

  <section class="founder-band">
    <p class="founder-line">The Brainchild of Rebecca Folwin<br>Ridge Lass Crew</p>
    <p class="mission">dedicated to coaching &amp; mentoring our girls<br>into strong, independent young women</p>
  </section>

  <h2 class="offer-heading">We look to offer</h2>
  <ul class="offer-list">
    <li><svg width="16" height="16" viewBox="0 0 16 16"><circle cx="8" cy="8" r="6" fill="none" stroke="#fff" stroke-width="2"/><path d="M5 8l2 2 4-4" fill="none" stroke="#fff" stroke-width="2"/></svg>Daily meditation</li>
    <li><svg width="16" height="16" viewBox="0 0 16 16"><circle cx="8" cy="8" r="6" fill="none" stroke="#fff" stroke-width="2"/><path d="M5 8l2 2 4-4" fill="none" stroke="#fff" stroke-width="2"/></svg>Healthy snacks</li>
    <li><svg width="16" height="16" viewBox="0 0 16 16"><circle cx="8" cy="8" r="6" fill="none" stroke="#fff" stroke-width="2"/><path d="M5 8l2 2 4-4" fill="none" stroke="#fff" stroke-width="2"/></svg>Dedicated homework time</li>
    <li><svg width="16" height="16" viewBox="0 0 16 16"><circle cx="8" cy="8" r="6" fill="none" stroke="#fff" stroke-width="2"/><path d="M5 8l2 2 4-4" fill="none" stroke="#fff" stroke-width="2"/></svg>Organised group activity, led by qualified instructors<br>(yoga, fitness class, soccer etc.)</li>
    <li><svg width="16" height="16" viewBox="0 0 16 16"><circle cx="8" cy="8" r="6" fill="none" stroke="#fff" stroke-width="2"/><path d="M5 8l2 2 4-4" fill="none" stroke="#fff" stroke-width="2"/></svg>Regular guests speakers</li>
    <li><svg width="16" height="16" viewBox="0 0 16 16"><circle cx="8" cy="8" r="6" fill="none" stroke="#fff" stroke-width="2"/><path d="M5 8l2 2 4-4" fill="none" stroke="#fff" stroke-width="2"/></svg>SOCIAL MEDIA FREE ZONE</li>
  </ul>

  <p class="hours-days">Open every afternoon and during school holidays</p>
  <p class="hours-time">3-6pm Monday to Friday</p>

  <footer class="contact-bar">
    <svg class="icon" style="left:16px;top:16px" width="44" height="44" viewBox="0 0 44 44"><circle cx="22" cy="22" r="22" fill="#b768aa"/><rect x="11" y="14" width="22" height="16" rx="2" fill="#fff"/><path d="M11 15l11 8 11-8" fill="none" stroke="#b768aa" stroke-width="2"/></svg>
    <p class="contact-text" style="left:79px;top:12px">e-Mail us<br>info@ridgelasscrew.example.au</p>
    <svg class="icon" style="left:24px;top:76px" width="24" height="24" viewBox="0 0 24 24"><rect width="24" height="24" rx="3" fill="var(--social-square)"/></svg>
    <p class="contact-text" style="left:73px;top:76px">http://fb.example/ridgelasscrew</p>

    <svg class="icon" style="left:325px;top:28px" width="50" height="50" viewBox="0 0 50 50"><circle cx="25" cy="25" r="25" fill="#b768aa"/><rect x="18" y="12" width="14" height="26" rx="3" fill="none" stroke="#fff" stroke-width="2"/><circle cx="25" cy="34" r="1.5" fill="#fff"/></svg>
    <p class="contact-text" style="left:394px;top:28px">Call Us Now<br>0455817396</p>

    <svg class="icon" style="left:575px;top:26px" width="50" height="50" viewBox="0 0 50 50"><circle cx="25" cy="25" r="25" fill="#b768aa"/><path d="M25 38c-6-8-9-12-9-16a9 9 0 0 1 18 0c0 4-3 8-9 16z" fill="#fff"/><circle cx="25" cy="22" r="3.5" fill="#b768aa"/></svg>
    <p class="contact-text" style="left:652px;top:14px">87 Pelham Pde,<br>Castlemere Vale<br><span class="contact-note">(across from Crestmoor Day Clinic)</span></p>
  </footer>
</main>
</body>
</html>
```